Red Mesa Greenworks Summit needs a marketing flyer

We need a full page graphic for our upcoming Forum that can also be converted into a website "header" for social media, etc.: "Red Mesa Greenworks Summit - Shaping Change Across the Made Landscape"

INTRODUCTION:
During the first week of August 2022, Q-VarDT is presenting the Red Mesa Greenworks Summit - Shaping Change Across the Made Landscape.

One of the most exciting aspects of this conference will be the bringing together of multiple organizations including for-profits and nonprofits, K-12’s and higher education, cities and counties and other governmental agencies, as well as architects, engineers, and contractors to collaboratively present and discuss issues and ideas related to sustainability, with a Texas focus.

This event will be a catalyst for public and private project owners to holistically gather information and momentum as we bring the resources and vision needed to achieve the goal of zero carbon emissions from the built environment by 2040, and address water, green space and the natural environment, transportation, equity, and funding, among other topics.

```html
<!DOCTYPE html>
<html lang="en">
<head>
<meta charset="UTF-8">
<title>Red Mesa Greenworks Summit – Header Banner</title>
<link rel="stylesheet" href="https://fonts.googleapis.com/css2?family=Montserrat:wght@400;600;700&display=swap">
<style>
  :root {
    --backdrop: #b3b3b3;
    --paper: #ffffff;
    --navy: #2c3f8d;
    --leaf: #8cb43b;
    --leaf-light: #cde37a;
    --leaf-mid: #a6cc45;
    --leaf-deep: #6f9a2a;
    --ink: #444444;
    --logo-blue: #3a4fa0;
  }
  * { box-sizing: border-box; margin: 0; padding: 0; }
  html, body {
    width: 1200px; height: 852px; overflow: hidden;
    background: var(--backdrop);
    font-family: "Montserrat", sans-serif;
  }
  .banner {
    position: absolute; left: 161px; top: 191px;
    width: 894px; height: 448px;
    background: var(--paper);
  }
  .brand {
    position: absolute; left: 49px; top: 45px;
    display: flex; align-items: center; gap: 12px;
  }
  .brand-dot {
    width: 54px; height: 54px; border-radius: 50%;
    background: var(--logo-blue);
  }
  .brand-name {
    font-size: 29px; font-weight: 600; color: var(--ink);
    letter-spacing: 0.5px;
  }
  .event-name {
    position: absolute; left: 37px; top: 141px;
    color: var(--ink); font-size: 23px; font-weight: 400; line-height: 31px;
  }
  .divider {
    position: absolute; left: 37px; top: 210px;
    width: 78px; height: 4px; background: var(--leaf);
  }
  .theme {
    position: absolute; left: 37px; top: 223px;
    color: var(--leaf); font-size: 29px; font-weight: 700;
    line-height: 38px; letter-spacing: 0.3px;
  }
  .illustration {
    position: absolute; left: 375px; top: 35px;
    width: 490px; height: 310px;
  }
  .footer-band {
    position: absolute; left: 0; top: 370px;
    width: 100%; height: 44px; background: var(--navy);
    display: flex; align-items: center; justify-content: space-between;
    padding: 0 168px 0 41px;
  }
  .social { display: flex; gap: 16px; list-style: none; }
  .social-item {
    color: var(--paper); font-size: 12px; font-weight: 600;
    display: flex; align-items: center; gap: 6px;
  }
  .social-item::before {
    content: ""; width: 6px; height: 6px; border-radius: 50%;
    background: var(--paper);
  }
  .web {
    display: flex; align-items: center; gap: 8px;
    color: var(--paper); font-size: 13.5px; letter-spacing: 0.3px;
  }
</style>
</head>
<body>
  <section class="banner">
    <div class="brand">
      <span class="brand-dot"></span>
      <span class="brand-name">Q-VarDT</span>
    </div>

    <h1 class="event-name">RED MESA<br>Greenworks Summit</h1>
    <div class="divider"></div>
    <h2 class="theme">SHAPING CHANGE<br>ACROSS THE MADE<br>LANDSCAPE</h2>

    <svg class="illustration" viewBox="0 0 490 310" role="img" aria-label="Green paper-cut illustration of a sustainable town with clouds, sun, wind turbines, trees and houses">
      <defs>
        <linearGradient id="town-tone" x1="0" y1="0" x2="0" y2="1">
          <stop offset="0" stop-color="var(--leaf-light)"/>
          <stop offset="0.55" stop-color="var(--leaf-mid)"/>
          <stop offset="1" stop-color="var(--leaf-deep)"/>
        </linearGradient>
        <radialGradient id="town-glow" cx="0.5" cy="0.35" r="0.55">
          <stop offset="0" stop-color="#ffffff" stop-opacity="0.45"/>
          <stop offset="1" stop-color="#ffffff" stop-opacity="0"/>
        </radialGradient>
      </defs>
      <path d="M18,305 A232,232 0 1 1 480,262 C400,250 330,270 250,290 C170,310 90,300 18,305 Z" fill="url(#town-tone)"/>
      <path d="M18,305 A232,232 0 1 1 480,262 C400,250 330,270 250,290 C170,310 90,300 18,305 Z" fill="url(#town-glow)"/>
    </svg>

    <footer class="footer-band">
      <ul class="social" aria-label="Social media">
        <li class="social-item">Pixloom</li>
        <li class="social-item">Friendlane</li>
        <li class="social-item">Chirpline</li>
      </ul>
      <div class="web">
        <svg width="16" height="16" viewBox="0 0 16 16" aria-hidden="true">
          <circle cx="8" cy="8" r="6.5" fill="none" stroke="#fff" stroke-width="1.6"/>
          <path d="M1.5 8h13M8 1.5c2.5 3 2.5 10 0 13M8 1.5c-2.5 3-2.5 10 0 13" fill="none" stroke="#fff" stroke-width="1.2"/>
        </svg>
        <span>www.q-vardt.meshpage.org</span>
      </div>
    </footer>
  </section>
</body>
</html>
```